Film Production Company Needs HTML Website Design

My production company, QuillanStudioWorks.com , needs to have an HTML design of our website. I would like a minotaur as the company symbol, as well as a hellfire in the background. Something dark and edgy, like we currently have, but different. The password to open the attached zip file is: KTRW3mze81Pvd62JGsQe
Please check out our website and include all of the tabs that are currently in the design, especially the Investor section.

Film Production

```html
<!DOCTYPE html>
<html lang="en">
<head>
<meta charset="utf-8">
<title>Quillan Studio Works – Investors</title>
<link rel="stylesheet" href="https://fonts.googleapis.com/css2?family=Marcellus&family=Cinzel:wght@700&family=Cambo&family=Open+Sans&display=swap">
<style>
:root{
  --page:#ffffff;
  --frame:#000000;
  --glow:#5a0000;
  --deep:#1a0000;
  --ember:#d4111a;
  --gold:#e0a428;
  --logo:#e8901c;
  --body-text:#f3e4bc;
  --hole:#3a0707;
  --footer-text:#f0a070;
  --nav-border:#4a0606;
}
*{margin:0;padding:0;box-sizing:border-box}
html,body{width:1200px;height:1000px;overflow:hidden;background:var(--page)}
.site{position:absolute;left:50px;top:37px;width:1108px;height:920px;background:
  radial-gradient(ellipse 620px 420px at 554px 470px,#260000 0%,rgba(0,0,0,0) 70%),
  linear-gradient(90deg,var(--glow) 0%,#140000 12%,#0a0000 50%,#140000 88%,var(--glow) 100%);overflow:hidden}
.site::before{content:"";position:absolute;left:0;top:0;width:100%;height:115px;background:var(--frame)}
.site::after{content:"";position:absolute;left:0;bottom:0;width:100%;height:140px;background:linear-gradient(rgba(0,0,0,0),#000 80%)}
.brand{position:absolute;left:0;width:100%;top:40px;text-align:center;z-index:2}
.brand-name{font-family:"Cinzel",serif;font-weight:700;font-size:74px;line-height:90px;color:var(--logo);letter-spacing:1px;padding-left:60px}
.brand-sub{font-family:"Cambo",serif;font-size:21px;letter-spacing:20px;color:var(--ember);margin-top:22px;padding-left:86px}
.main-nav{position:absolute;left:13px;top:198px;width:1087px;height:52px;background:#050000;border:4px solid var(--nav-border);border-radius:10px;box-shadow:0 0 8px #6a0000;z-index:2}
.main-nav a{position:absolute;top:9px;font-family:"Marcellus",serif;font-size:19px;color:var(--ember);text-decoration:none;letter-spacing:1px;transform:translateX(-50%)}
.main-nav a.is-active{color:var(--gold);top:6px}
.nav-sep{position:absolute;top:9px;width:1px;height:24px;background:#444}
.content-panel{position:absolute;left:35px;top:261px;width:1043px;height:484px;background:#000;z-index:1}
.film-hole{position:absolute;width:102px;height:54px;border-radius:14px;background:var(--hole)}
.reel-art{position:absolute;left:265px;top:80px;width:620px;height:360px;background:radial-gradient(ellipse at 40% 45%,rgba(110,110,110,.35),rgba(60,60,60,.15) 45%,rgba(0,0,0,0) 75%)}
.content-text{position:absolute;left:163px;top:24px;width:715px;font-family:"Cambo",serif;font-size:11px;line-height:18.2px;color:var(--body-text);letter-spacing:-.2px}
.seating-art{position:absolute;left:250px;top:745px;width:660px;height:130px;background:radial-gradient(ellipse at 50% 40%,rgba(80,90,100,.45),rgba(0,0,0,0) 70%);z-index:1}
.social{position:absolute;left:22px;top:864px;display:flex;gap:10px;z-index:3}
.social span{width:32px;height:30px;background:#1e1408}
.footer-note{position:absolute;left:0;width:100%;top:873px;text-align:center;font-family:"Open Sans",sans-serif;font-size:10px;color:var(--footer-text);z-index:3}
</style>
</head>
<body>
<div class="site">
  <header class="brand">
    <div class="brand-name">QUILLAN STUDIO</div>
    <div class="brand-sub">WORKS</div>
  </header>

  <nav class="main-nav">
    <a href="#" style="left:135px;top:11px">Home</a>
    <span class="nav-sep" style="left:198px"></span>
    <a href="#" style="left:283px">About Us</a>
    <span class="nav-sep" style="left:361px"></span>
    <a href="#" style="left:426px">News</a>
    <span class="nav-sep" style="left:481px"></span>
    <a href="#" style="left:576px">Productions</a>
    <span class="nav-sep" style="left:666px"></span>
    <a href="#" class="is-active" style="left:742px">Investors</a>
    <span class="nav-sep" style="left:828px"></span>
    <a href="#" style="left:911px">Contact Us</a>
  </nav>

  <main class="content-panel">
    <div class="film-hole" style="left:28px;top:44px"></div>
    <div class="film-hole" style="left:28px;top:130px"></div>
    <div class="film-hole" style="left:28px;top:216px"></div>
    <div class="film-hole" style="left:28px;top:302px"></div>
    <div class="film-hole" style="left:28px;top:388px"></div>
    <div class="film-hole" style="left:914px;top:44px"></div>
    <div class="film-hole" style="left:914px;top:130px"></div>
    <div class="film-hole" style="left:914px;top:216px"></div>
    <div class="film-hole" style="left:914px;top:302px"></div>
    <div class="film-hole" style="left:914px;top:388px"></div>

    <div class="reel-art" role="img" aria-label="Faded film reel with film strip and banknotes"></div>

    <div class="content-text">
      Sed laoreet aliquam leo ut tellus dolor dapi eget elementum vel cursus elei fend eliter Aenean auctor wisi et urna aliquam erat. volutpat. Duis ac turpis. Integer rutrum ante eu lacus. Sed laoreet<br>
      aliquam leo ut tellus dolor dapi eget elementum vel cursus elei fend eliter Aenean auctor wisi et urna aliquam erat. volutp<br>
      ce turna Sed laoreet aliquam leo ut tellus dolor dapi eget elementum vel cursus elei fend eliter Aenean auctor wisi et urna aliquam erat. volutp<br>
      Sed laoreet aliquam leo ut tellus dolor dapi eget elementum vel cursus elei fend eliter Aenean auctor wisi et urna aliquam erat. volutp<br>
      Sed laoreet aliquam leo ut tellus dolor dapi eget elementum vel cursus elei fend eliSed laoreet aliquam leo ut tellus dolor dapi eget elementum vel cursus elei fend eliter Aenean auctor w<br>
      isi et urna aliquam erat. volutp<br>
      Sed laoreet aliquam leo ut tellus dolor dapi eget elementum vel cursus elei fend eliter Aenean auctor wisi et urna aliquam erat. volutp<br>
      Sed laoreet aliquam leo ut tellus dolor dapi eget elementum vel cursus elei fend eli<br>
      aliquam erat. volutpSed laoreet aliquam leo ut tellus dolor dapi eget elementum vel cursus elei fend eliter Aenean auctor wisi et urna aliquam erat. volutp<br>
      Sed laoreet aliquam leo ut tellus dolor dapi eget elementum vel cursus elei fend eliter Aenean auctor wisi<br>
      Sed laoreet aliquam leo ut tellus dolor dapi eget elementum vel cuSed laoreet aliquam leo ut tellus dolor dapi eget elementum vel cursus elei fend eliter Aenean auctor wisi et urna aliquam erat. volutp<br>
      Sed laoreet aliquam leo ut tellus dolor dapi eget elementum vel cursus elei fend eliter Aenean auctor wisi<br>
      rsus elei fend eliter Aenean auctor wisi et urna aliquam erat. volutp<br>
      Sed laoreet aliquam leo ut tellus dolor dapi eget elementum vel cursus elei fend eliter Aenean auctor wisi et urna aliquam erat. volutp<br>
      Sed laoreet aliquam leo ut tellus dolor dapi eget elementum vel cursus elei fend eliter Aenean a<br>
      uctor wisi et urna aliquam erat. volutpSed laoreet aliquam leo ut tellus dolor dapi eget elementum vel cursus elei fend eliter Aenean auctor wisi et urna aliquam erat. volutp<br>
      Sed laoreet aliquam leo ut tellus dolor dapi eget elementum vel cursus elei fend eliter Aenean auctor wisi
    </div>
  </main>

  <div class="seating-art" role="img" aria-label="Rows of cinema seats fading into darkness"></div>

  <div class="social" aria-label="Social links">
    <span></span><span></span><span></span><span></span>
  </div>
  <footer class="footer-note">Quillan Studio © 2014 . Privacy Policy</footer>
</div>
</body>
</html>
```